How likely are people to engage in social distancing? We need a good illustration to show the data!

We surveyed U.S. adults March 20th - 24th, 2020 and asked how likely they were to engage in social distancing (and other COVID-19 related health behaviors). What did the survey find? Basically, most people intend to engage in social distancing behaviors (e.g., avoiding large crowds) and other behaviors that reduce the spread of COVID-19 (e.g., washing hands at least 20 seconds). When most people intend to engage in a behavior, then public health professionals try to leverage that to move more people to act.
Now we need innovative and professional images that attempt to communicate one or all of these findings. The specific findings are nicely summarized in the attached document. For example, 82% of participants intend to engage in social distancing.
What sort of visual are we looking for? Our preference is for an original illustration (or set of illustrations). Our preference is for (creative and powerful illustrations, but we are also open to the creative and well-executed infographics.
We need these images fast . We will award monetary prizes to the 3 best designs. If we like more than that, then we might purchase more (e.g., in past contests, we have purchased as many as 30 designs).
What we will need:
(1) The illustrations must be original and we will need the photoshop and/or illustrator files for all artwork.
(2) You can illustrate all of the findings or just one of them. We need creative approaches that do a lucid job of bringing the data to life. Most people intend to engage in these behaviors. How to communicate that? Republicans and Democrats do not differ in their intentions; how to communicate that?
(3) The illustration should say, somewhere: "Based on a survey of 400 U.S. adults conducted March 20 - 24th, 2020."

U.S. Adults

• Original illustrations based on the findings of the survey (see attached document).

```html
<!DOCTYPE html>
<html lang="en">
<head>
<meta charset="utf-8">
<title>Health Behaviors by Party</title>
<link rel="stylesheet" href="https://fonts.googleapis.com/css2?family=Alegreya+Sans:ital,wght@0,300;0,400;1,300&display=swap">
<style>
  :root {
    --page: #ffffff;
    --ink: #6e6e6e;
    --rep: #e57d8c;
    --rep-light: #efa0ab;
    --rep-text: #e26d7e;
    --dem: #8fb0e6;
    --dem-light: #a9c3ef;
    --dem-text: #8aaee6;
    --grid: #ececec;
    --elephant: #b9b9b9;
    --donkey: #b7a894;
    --stool: #e2a24a;
    --virus: #b6553e;
  }
  * { margin: 0; padding: 0; box-sizing: border-box; }
  html, body { width: 800px; height: 1200px; overflow: hidden; background: var(--page); }
  body { font-family: "Alegreya Sans", sans-serif; color: var(--ink); position: relative; }

  .chart { position: absolute; left: 0; top: 50px; width: 800px; height: 640px; }
  .chart__grid { position: absolute; left: 340px; top: 0; width: 420px; height: 640px; }
  .chart__gridline { position: absolute; top: 0; bottom: 0; width: 1px; background: var(--grid); }
  .chart__axis { position: absolute; left: 340px; top: 0; width: 1px; height: 640px; background: #dcdcdc; }

  .row { position: absolute; left: 0; width: 800px; height: 92px; }
  .row__label {
    position: absolute; left: 40px; width: 280px; top: 50%; transform: translateY(-50%);
    text-align: right; font-weight: 300; font-size: 21px; line-height: 1.1; color: var(--ink);
  }
  .bar { position: absolute; left: 341px; height: 42px; }
  .bar--rep { top: 4px; background: linear-gradient(180deg, var(--rep-light), var(--rep)); }
  .bar--dem { top: 46px; background: linear-gradient(180deg, var(--dem-light), var(--dem)); }
  .bar__value { position: absolute; left: 100%; margin-left: 8px; top: -6px; font-size: 20px; font-weight: 400; }
  .bar--rep .bar__value { color: var(--rep-text); }
  .bar--dem .bar__value { color: var(--dem-text); top: auto; bottom: 20px; }

  .legend { position: absolute; left: 360px; top: 720px; display: flex; gap: 48px; font-size: 22px; font-weight: 400; }
  .legend__item { display: flex; align-items: center; gap: 12px; }
  .legend__swatch { width: 28px; height: 28px; }
  .legend__swatch--rep { background: var(--rep); }
  .legend__swatch--dem { background: #5f82cf; }

  .illustration-parties {
    position: absolute; left: 420px; top: 780px; width: 380px; height: 330px;
    background: radial-gradient(ellipse at 40% 40%, #cfcfcf 0%, var(--elephant) 45%, var(--donkey) 75%, #f3e2c6 100%);
    border-radius: 40% 0 0 30%;
  }
  .illustration-virus {
    position: absolute; left: 140px; top: 1040px; width: 70px; height: 70px; border-radius: 50%;
    background: radial-gradient(circle at 45% 45%, #e6a04a 0%, var(--virus) 55%, #7a5a55 100%);
  }

  .footnote {
    position: absolute; left: 0; right: 0; top: 1150px; text-align: center;
    font-style: italic; font-weight: 300; font-size: 19px; color: var(--ink);
  }
</style>
</head>
<body>
  <section class="chart" aria-label="Intended health behaviors by party">
    <div class="chart__grid">
      <span class="chart__gridline" style="left:84px"></span>
      <span class="chart__gridline" style="left:168px"></span>
      <span class="chart__gridline" style="left:252px"></span>
      <span class="chart__gridline" style="left:336px"></span>
      <span class="chart__gridline" style="left:420px"></span>
    </div>
    <div class="chart__axis"></div>

    <div class="row" style="top:20px">
      <p class="row__label">Cancel social activities</p>
      <div class="bar bar--rep" style="width:344px"><span class="bar__value">82%</span></div>
      <div class="bar bar--dem" style="width:336px"><span class="bar__value">80%</span></div>
    </div>
    <div class="row" style="top:140px">
      <p class="row__label">Put distance between yourself and other people</p>
      <div class="bar bar--rep" style="width:353px"><span class="bar__value">84%</span></div>
      <div class="bar bar--dem" style="width:365px"><span class="bar__value">87%</span></div>
    </div>
    <div class="row" style="top:260px">
      <p class="row__label">Wash hands at least 20 seconds</p>
      <div class="bar bar--rep" style="width:365px"><span class="bar__value">87%</span></div>
      <div class="bar bar--dem" style="width:370px"><span class="bar__value">88%</span></div>
    </div>
    <div class="row" style="top:380px">
      <p class="row__label">Use hand sanitizer</p>
      <div class="bar bar--rep" style="width:365px"><span class="bar__value">87%</span></div>
      <div class="bar bar--dem" style="width:353px"><span class="bar__value">84%</span></div>
    </div>
    <div class="row" style="top:500px">
      <p class="row__label">Avoid touching your eyes, nose, and mouth</p>
      <div class="bar bar--rep" style="width:336px"><span class="bar__value">80%</span></div>
      <div class="bar bar--dem" style="width:344px"><span class="bar__value">82%</span></div>
    </div>
  </section>

  <div class="legend">
    <span class="legend__item"><span class="legend__swatch legend__swatch--rep"></span>Republican</span>
    <span class="legend__item"><span class="legend__swatch legend__swatch--dem"></span>Democrat</span>
  </div>

  <div class="illustration-parties" role="img" aria-label="Illustration of an elephant and a donkey standing together on a wooden stool"></div>
  <div class="illustration-virus" role="img" aria-label="Small illustration of a coronavirus particle on the ground"></div>

  <p class="footnote">*Based on a survey of 400 U.S. adults conducted March 20 - 24th, 2020.</p>
</body>
</html>
```